Brightvale cleaning and maintenance company

An expansive website whereby we can advertise our commercial cleaning and maintenance services across a service portfolio of commercial cleaning and property maintenance. Whereby potential skilled resources can deposit there resume so we can collaborate and match candidates to a broad range of cleaning and maintenance jobs/projects.
Updates

Looking for more extensive ideas so the front page can change pictures on it with the focus for Brightvale Commercial Cleaning and Maintenance. Also need to bring in all the portfolios we offer including 1. Equipment Cleaning and Sanitisation Services 2. High pressure gurney and play ground equipment cleaning 3. General Cleaning and Property Facilities Management 4. Project and Recruiting Services, to allow for potential professional cleaners, handy man, mechanics, warehousing resources , electricians to deposit there resume. Most of the designers have stuck with the old portfolio categories , however the portfolio of services we offer has been updated so that needs to be reflected in the website. Also not necessary to use all my original photos I would like the opening page of the website to perhaps be able to change and have different pictures is that possible thank you

```html
<!DOCTYPE html>
<html lang="en">
<head>
<meta charset="utf-8">
<title>Brightvale – Commercial Cleaning &amp; Maintenance</title>
<link href="https://fonts.googleapis.com/css2?family=Roboto+Slab:wght@300;400;500;700&family=Lato:wght@400;700&display=swap" rel="stylesheet">
<style>
:root{
  --navy:#1d3f7c;
  --orange:#f4420f;
  --blue:#2b5fa6;
  --ink:#222;
  --line:#d8d8d8;
  --footer:#1b1b1b;
  --white:#fff;
  --slab:"Roboto Slab",Georgia,serif;
}
*{box-sizing:border-box;margin:0;padding:0}
html,body{width:1200px;height:5146px;overflow:hidden}
body{font-family:"Lato",Arial,sans-serif;color:var(--ink);background:var(--white);position:relative}
section,header,footer,nav{position:relative;width:1200px}
.abs{position:absolute}
.btn{position:absolute;display:flex;align-items:center;justify-content:center;font-family:var(--slab);font-weight:700;font-size:14px;color:var(--white);background:var(--orange);text-transform:uppercase;letter-spacing:.3px}
.mark{position:absolute;border-radius:50%;background:var(--navy)}

/* top nav */
.topbar{height:38px}
.topbar ul{position:absolute;left:262px;width:804px;height:38px;background:var(--navy);display:flex;list-style:none;justify-content:space-between;align-items:center;padding-right:10px}
.topbar li{font-family:var(--slab);font-weight:700;font-size:13px;color:var(--white);height:38px;line-height:38px;padding:0 14px}
.topbar li.active{background:var(--white);color:var(--navy)}

/* header */
.site-header{height:96px}
.brand{position:absolute;left:144px;top:18px;display:flex;align-items:center;gap:12px}
.brand .dot{width:56px;height:56px;border-radius:50%;background:var(--navy)}
.brand span{font-family:var(--slab);font-weight:400;font-size:44px;color:var(--orange)}
.call{position:absolute;left:556px;top:24px;display:flex;gap:10px;align-items:center}
.call small{display:block;font-size:13px;color:var(--ink)}
.call strong{display:block;font-family:var(--slab);font-size:22px;color:var(--navy);font-weight:700}
.search{position:absolute;left:792px;top:30px;width:264px;height:36px;border:1px solid #bbb;border-radius:18px;font-size:12px;color:#555;padding:10px 18px}
.search svg{position:absolute;right:14px;top:11px}

/* hero */
.hero{height:1048px;background:linear-gradient(180deg,#2b5fa6 0%,#1f4d92 60%,#2d6bb5 100%)}
.hero-photo{position:absolute;left:0;top:0;width:1200px;height:740px;background:linear-gradient(160deg,#9aa0a4 0%,#6f7579 45%,#4d5357 100%)}
.hero h1{position:absolute;left:0;width:1200px;top:170px;text-align:center;font-family:var(--slab);font-weight:300;font-size:96px;line-height:110px;color:var(--white)}
.hero .sub{position:absolute;left:0;width:1200px;top:278px;text-align:center;font-family:var(--slab);font-weight:300;font-size:40px;line-height:40px;color:var(--white)}
.hero .arrow{position:absolute;top:262px;width:38px;height:38px;border-radius:50%;background:rgba(0,0,0,.55)}
.hero .arrow svg{position:absolute;left:12px;top:11px}
.welcome h2{position:absolute;left:0;width:1200px;top:696px;text-align:center;font-family:var(--slab);font-weight:500;font-size:38px;color:var(--white)}
.welcome .rule{position:absolute;left:562px;top:768px;width:76px;height:3px;background:var(--white)}
.welcome p{position:absolute;left:196px;width:808px;top:790px;text-align:center;font-size:14.5px;line-height:25px;color:#e8eefa}

/* services */
.services-head{height:178px}
.sec-title{position:absolute;left:0;width:1200px;text-align:center;font-family:var(--slab);font-weight:700;font-size:36px;color:var(--ink)}
.services{height:816px}
.card{position:absolute;overflow:hidden}
.card .photo{position:absolute;left:0;top:0;width:100%}
.card .bar{position:absolute;left:0;width:100%;background:var(--orange)}
.card h3{position:absolute;left:18px;font-family:var(--slab);font-weight:700;font-size:18px;color:var(--white);white-space:nowrap}
.card.small h3{font-size:17px}
.card p{position:absolute;left:18px;font-size:12.5px;line-height:15px;color:#ffe5da}
.card .more{position:absolute;right:22px;width:124px;height:36px;border:2px solid var(--white);color:var(--white);font-family:var(--slab);font-weight:700;font-size:12px;display:flex;align-items:center;justify-content:center}
.card .upload{position:absolute;left:18px;top:360px;height:24px;padding:0 12px;border:2px solid var(--white);color:var(--white);font-family:var(--slab);font-weight:700;font-size:11px;display:flex;align-items:center;gap:6px}

/* about */
.about{height:592px}
.about h2{position:absolute;left:144px;top:106px;width:480px;font-family:var(--slab);font-weight:300;font-size:25px;line-height:29px;color:var(--ink)}
.about .divider{position:absolute;left:144px;top:244px;width:462px;height:1px;background:var(--line)}
.about p{position:absolute;left:144px;top:268px;width:460px;font-size:13.5px;line-height:25px;color:var(--ink)}
.clients{position:absolute;top:338px;list-style:none;font-size:12.5px;line-height:23px}
.clients li{padding-left:22px;position:relative}
.clients li::before{content:"";position:absolute;left:2px;top:7px;width:10px;height:10px;border-radius:50%;background:var(--navy)}
.about .frame{position:absolute;left:650px;top:94px;width:402px;height:420px;border:1px solid #999}
.about .team{position:absolute;left:662px;top:104px;width:396px;height:414px;background:linear-gradient(180deg,#e6ebe6 0%,#3f8b4e 60%,#2e6e3c 100%)}

/* coverage */
.coverage{height:650px;background:linear-gradient(180deg,#ffffff 0%,#cfe4f6 14%,#7fb9ea 40%,#4d97dc 75%,#3b86d2 100%)}
.coverage h2{position:absolute;left:0;width:1200px;top:364px;text-align:center;font-family:var(--slab);font-weight:500;font-size:36px;line-height:42px;color:var(--white)}

/* blog */
.blog{height:700px}
.post{position:absolute;border:1px solid var(--line);background:var(--white)}
.post .thumb{position:absolute}
.post .date{position:absolute;display:flex;align-items:center;gap:8px;font-family:var(--slab);font-weight:700;font-size:13.5px;color:var(--orange)}
.post .date i{width:18px;height:18px;border-radius:50%;background:var(--navy);display:block}
.post h4{position:absolute;font-family:var(--slab);font-weight:700;font-size:14px;line-height:20px;color:var(--ink)}
.post p{position:absolute;font-size:13px;line-height:21px;color:#444}

/* testimonials */
.testimonials{height:504px;background:linear-gradient(180deg,#f24a14 0%,#f35220 60%,#f0420c 100%)}
.testimonials h2{position:absolute;left:0;width:1200px;top:98px;text-align:center;font-family:var(--slab);font-weight:500;font-size:38px;color:var(--white)}
.testimonials blockquote{position:absolute;left:256px;width:688px;top:176px;text-align:center;font-size:16.5px;line-height:26px;color:var(--white)}
.testimonials .q{font-family:var(--slab);font-weight:700;font-size:20px}
.avatar{position:absolute;border-radius:50%;border:3px solid var(--white);background:linear-gradient(160deg,#c9a890,#7d6354)}
.testimonials .name{position:absolute;left:500px;width:134px;top:414px;text-align:center;font-size:12px;font-weight:700;color:var(--white)}

/* footer */
.site-footer{height:524px;background:var(--footer);color:var(--white)}
.site-footer h5{position:absolute;top:52px;font-family:var(--slab);font-weight:700;font-size:21px}
.site-footer .uline{position:absolute;top:98px;width:60px;height:2px;background:var(--white)}
.field{position:absolute;height:34px;border:1px solid #888;font-size:11px;color:#ddd;padding:10px 12px}
.contact-item{position:absolute;left:606px;display:flex;gap:16px;font-size:13px;line-height:19px;color:#ddd}
.contact-item .ico{width:32px;height:32px;border-radius:50%;border:1.5px solid #ddd;flex:none;position:relative}
.contact-item .ico svg{position:absolute;left:7px;top:7px}
.quick{position:absolute;left:924px;top:146px;list-style:none;font-size:13px;line-height:28px;color:#ddd}
.copy{position:absolute;left:0;width:1200px;top:474px;text-align:center;font-size:13px;color:#ccc}
.copyline{position:absolute;left:0;top:448px;width:1200px;height:1px;background:#333}
</style>
</head>
<body>

<nav class="topbar">
  <ul>
    <li class="active">HOME</li><li>SERVICES</li><li>ABOUT US</li><li>OUR PEOPLE</li><li>SAFETY &amp; COMPLIANCE</li><li>CAREERS</li><li>CONTACT</li>
  </ul>
</nav>

<header class="site-header">
  <div class="brand"><div class="dot"></div><span>Brightvale</span></div>
  <div class="call">
    <svg width="34" height="34" viewBox="0 0 24 24" fill="none" stroke="#666" stroke-width="1.4"><path d="M5 3h4l2 5-2.5 1.5a11 11 0 0 0 6 6L16 13l5 2v4a2 2 0 0 1-2 2A17 17 0 0 1 3 5a2 2 0 0 1 2-2z"/></svg>
    <div><small>Call Us Today!</small><strong>(07) 5550 1284</strong></div>
  </div>
  <div class="search">Search here
    <svg width="13" height="13" viewBox="0 0 24 24" fill="none" stroke="#333" stroke-width="3"><circle cx="10" cy="10" r="7"/><path d="M15 15l6 6"/></svg>
  </div>
</header>

<section class="hero">
  <div class="hero-photo" role="img" aria-label="Rotating hero photos: clean stainless steel commercial kitchen"></div>
  <svg class="abs" style="left:0;top:600px" width="1200" height="142" viewBox="0 0 1200 142" preserveAspectRatio="none">
    <path d="M0 76 C260 40 480 150 700 124 C900 100 1060 44 1200 60 L1200 142 L0 142Z" fill="#2b5fa6"/>
    <path d="M0 72 C260 36 480 146 700 120 C900 96 1060 40 1200 56" fill="none" stroke="#4f82c4" stroke-width="3"/>
  </svg>
  <h1>Brightvale</h1>
  <div class="sub">our commercial cleaning and<br>maintenance services</div>
  <div class="btn" style="left:522px;top:516px;width:156px;height:40px;top:516px"></div>
  <div class="arrow" style="left:59px"><svg width="14" height="16" viewBox="0 0 14 16" fill="none" stroke="#fff" stroke-width="2"><path d="M10 1L3 8l7 7"/></svg></div>
  <div class="arrow" style="left:1103px"><svg width="14" height="16" viewBox="0 0 14 16" fill="none" stroke="#fff" stroke-width="2"><path d="M4 1l7 7-7 7"/></svg></div>
  <div class="welcome">
    <h2>Welcome to Brightvale</h2>
    <div class="rule"></div>
    <p>Lorem ipsum dolor sit amet, consectetur adipiscing elit, sed do eiusmod tempor incididunt ut labore et dolore magna aliqua. Ut enim ad minim veniam, quis nostrud exercitation ullamco laboris nisi ut aliquip ex ea commodo consequat. Duis aute irure dolor in reprehenderit in voluptate velit esse cillum dolore eu fugiat nulla pariatur. Excepteur sint occaecat cupidatat non proident, sunt in culpa qui officia deserunt mollit anim id est laborum</p>
    <div class="btn" style="left:532px;top:926px;width:136px;height:40px">Read More</div>
  </div>
</section>

<section class="services-head">
  <div class="mark" style="left:584px;top:56px;width:32px;height:32px"></div>
  <h2 class="sec-title" style="top:88px">Our Services</h2>
</section>

<section class="services">
  <article class="card" style="left:0;top:0;width:598px;height:420px">
    <div class="photo" style="height:318px;background:linear-gradient(160deg,#c7c9cb,#8a8f94 60%,#6a7a8a)" role="img" aria-label="Soft serve machine dispensing an ice cream cone"></div>
    <div class="bar" style="top:318px;height:102px"></div>
    <h3 style="top:340px">Equipment Cleaning &amp; Sanitisation</h3>
    <p style="top:368px;width:400px">Full cleaning, sanitising and tune up kit service for food service and commercial equipment.</p>
    <div class="more" style="top:356px">READ MORE</div>
  </article>
  <article class="card" style="left:602px;top:0;width:598px;height:420px">
    <div class="photo" style="height:318px;background:linear-gradient(160deg,#d98c6a,#b84848 45%,#c24b5a 70%,#7d6a58)" role="img" aria-label="Family playing on colourful playground equipment"></div>
    <div class="bar" style="top:318px;height:102px"></div>
    <h3 style="top:340px">High Pressure Gurney &amp; Playground</h3>
    <p style="top:368px;width:400px">High pressure gurney cleaning and sanitisation of playground equipment and play areas.</p>
    <div class="more" style="top:356px">READ MORE</div>
  </article>
  <article class="card small" style="left:0;top:426px;width:398px;height:390px">
    <div class="photo" style="height:280px;background:linear-gradient(160deg,#b8b4aa,#7b756a 55%,#5b5248)" role="img" aria-label="Commercial restaurant kitchen with steel benches"></div>
    <div class="bar" style="top:280px;height:110px"></div>
    <h3 style="top:302px">General Cleaning</h3>
    <p style="top:330px;width:350px">Complete commercial kitchen, dining, office and bathroom area cleaning service.</p>
  </article>
  <article class="card small" style="left:401px;top:426px;width:398px;height:390px">
    <div class="photo" style="height:280px;background:linear-gradient(160deg,#8a8f6a,#a6a79a 45%,#6e6a50)" role="img" aria-label="Maintenance work on a commercial property"></div>
    <div class="bar" style="top:280px;height:110px"></div>
    <h3 style="top:302px">Property Facilities Management</h3>
    <p style="top:330px;width:350px">Planned maintenance, repairs and facilities management for commercial properties.</p>
  </article>
  <article class="card small" style="left:802px;top:426px;width:398px;height:390px">
    <div class="photo" style="height:280px;background:linear-gradient(160deg,#c4c6c8,#8c8e90 50%,#8a5a3a)" role="img" aria-label="Tradespeople ready for a project"></div>
    <div class="bar" style="top:280px;height:110px"></div>
    <h3 style="top:302px">Project &amp; Recruiting Services</h3>
    <p style="top:326px;width:360px">Cleaners, handymen, mechanics, warehousing staff and electricians: join our team.</p>
    <div class="upload">
      <svg width="11" height="11" viewBox="0 0 12 12" fill="none" stroke="#fff" stroke-width="1.8"><path d="M6 9V1M2.5 4.5L6 1l3.5 3.5M1 11h10"/></svg>UPLOAD YOUR RESUME
    </div>
  </article>
</section>

<section class="about">
  <h2>Brightvale has established a strong reputation as being reliable, responsive and dedicated to fulfilling our customers and partners cleaning service needs.</h2>
  <div class="divider"></div>
  <p>This reputation is reflected in the organisations that have trusted us to support them both locally and nationally, including:</p>
  <ul class="clients" style="left:146px">
    <li>Golden Crumb Chicken</li><li>Burger Lane</li><li>Fizzwell Beverages</li><li>Hearty Grill</li>
  </ul>
  <ul class="clients" style="left:370px">
    <li>Splash Cove, Reel Park</li><li>Ocean Parade</li><li>Kestrel Supply Pty Ltd</li><li>Hartwell</li>
  </ul>
  <div class="btn" style="left:146px;top:448px;width:138px;height:40px;background:var(--navy)">Read More</div>
  <div class="frame"></div>
  <div class="team" role="img" aria-label="Team of three cleaning staff in green aprons"></div>
</section>

<section class="coverage">
  <svg class="abs" style="left:0;top:0" width="1200" height="170" viewBox="0 0 1200 170" preserveAspectRatio="none" role="img" aria-label="Splashing water surface">
    <path d="M0 30 C120 10 220 40 320 60 C420 90 480 120 560 110 C640 100 700 70 780 80 C880 95 960 40 1060 20 C1120 10 1170 20 1200 30 L1200 130 C1000 140 800 150 600 150 C400 150 200 140 0 130Z" fill="#1f5f98"/>
    <path d="M0 70 C200 90 400 140 600 140 C800 140 1000 90 1200 70 L1200 170 L0 170Z" fill="#7fb9ea" opacity=".8"/>
  </svg>
  <div class="mark" style="left:564px;top:290px;width:72px;height:72px"></div>
  <h2>Servicing Metropolitan Sydney,<br>Brisbane, Melbourne, Adelaide, Newcastle<br>and Regional areas as required.</h2>
  <div class="btn" style="left:524px;top:516px;width:152px;height:40px">Get A Quote</div>
</section>

<section class="blog">
  <div class="mark" style="left:580px;top:60px;width:40px;height:40px"></div>
  <h2 class="sec-title" style="top:102px;font-weight:500;font-size:38px">Latest Blog</h2>

  <article class="post" style="left:144px;top:194px;width:314px;height:422px">
    <div class="thumb" style="left:0;top:0;width:312px;height:212px;background:linear-gradient(160deg,#b9bec2,#7e858b 55%,#5c6268)" role="img" aria-label="Stainless steel dispensing machine"></div>
    <div class="date" style="left:16px;top:238px"><i></i>JAN 15,2020</div>
    <h4 style="left:16px;top:276px;width:280px">Nemo Enim Ipsam Voluptatem Quia Voluptas Sit</h4>
    <p style="left:16px;top:328px;width:280px">Sed ut perspiciatis unde omnis iste natus error sit voluptatem accusantium doloque laium, totam rem aperiam</p>
  </article>

  <article class="post" style="left:480px;top:194px;width:578px;height:200px">
    <div class="thumb" style="left:0;top:0;width:222px;height:198px;background:linear-gradient(160deg,#3a5a4a,#3aa7a0 55%,#1e6e74)" role="img" aria-label="Hand holding a blue frozen drink cup"></div>
    <div class="date" style="left:252px;top:24px"><i></i>JAN 15,2020</div>
    <h4 style="left:252px;top:60px;width:300px">Nemo Enim Ipsam Voluptatem Quia Voluptas Sit</h4>
    <p style="left:252px;top:104px;width:306px">Sed ut perspiciatis unde omnis iste natus error sit voluptatem accusantium doloremque laium, totam rem aperiam, eaque</p>
  </article>

  <article class="post" style="left:480px;top:410px;width:578px;height:202px">
    <div class="thumb" style="left:0;top:0;width:222px;height:200px;background:linear-gradient(160deg,#9aa0a6,#4e555c 55%,#2e3338)" role="img" aria-label="Machine parts laid out for cleaning"></div>
    <div class="date" style="left:252px;top:24px"><i></i>JAN 15,2020</div>
    <h4 style="left:252px;top:60px;width:300px">Nemo Enim Ipsam Voluptatem Quia Voluptas Sit</h4>
    <p style="left:252px;top:104px;width:306px">Sed ut perspiciatis unde omnis iste natus error sit voluptatem accusantium doloremque laium, totam rem aperiam, eaque</p>
  </article>
</section>

<section class="testimonials">
  <div class="mark" style="left:578px;top:58px;width:44px;height:44px;background:var(--white)"></div>
  <h2>Testimonials</h2>
  <blockquote><span class="q">&ldquo;</span> Lorem ipsum dolor sit amet, consectetur adipiscing elit, sed do eiusmod tempor incididunt ut labore et dolore magna aliqua. Ut enim ad minim veniam, quis nostrud exercitation ullamco laboris nisi ut aliquip ex ea commodo consequat. Duis aute irure dolor in reprehenderit in voluptate velit esse cillum dolore eu fugiat nulla pariatur. Excepteur sint occaecat cupidatat non proident <span class="q">&rdquo;</span></blockquote>
  <svg class="abs" style="left:430px;top:362px" width="10" height="16" viewBox="0 0 10 16" fill="none" stroke="#fff" stroke-width="2"><path d="M8 1L2 8l6 7"/></svg>
  <svg class="abs" style="left:758px;top:362px" width="10" height="16" viewBox="0 0 10 16" fill="none" stroke="#fff" stroke-width="2"><path d="M2 1l6 7-6 7"/></svg>
  <div class="avatar" style="left:468px;top:342px;width:56px;height:56px" role="img" aria-label="Client portrait"></div>
  <div class="avatar" style="left:528px;top:332px;width:76px;height:76px" role="img" aria-label="Portrait of John Doe"></div>
  <div class="avatar" style="left:608px;top:342px;width:56px;height:56px" role="img" aria-label="Client portrait"></div>
  <div class="avatar" style="left:678px;top:342px;width:56px;height:56px" role="img" aria-label="Client portrait"></div>
  <div class="name">JOHN DOE</div>
</section>

<footer class="site-footer">
  <h5 style="left:144px">Get A Quote</h5><div class="uline" style="left:144px"></div>
  <div class="field" style="left:144px;top:146px;width:202px">First Name</div>
  <div class="field" style="left:360px;top:146px;width:202px">Last Name</div>
  <div class="field" style="left:144px;top:194px;width:202px">Phone Number</div>
  <div class="field" style="left:360px;top:194px;width:202px">Email Address</div>
  <div class="field" style="left:144px;top:242px;width:418px;height:60px">Message</div>
  <div class="btn" style="left:144px;top:336px;width:178px;height:36px;font-size:13px">Submit</div>

  <h5 style="left:606px">Contact Us</h5><div class="uline" style="left:606px"></div>
  <div class="contact-item" style="top:140px">
    <span class="ico"><svg width="16" height="16" viewBox="0 0 24 24" fill="none" stroke="#ddd" stroke-width="2"><path d="M12 22s7-7 7-12a7 7 0 0 0-14 0c0 5 7 12 7 12z"/><circle cx="12" cy="10" r="2.5"/></svg></span>
    <div>Address:<br>118 Harbour View Road<br>Southport, QLD 4215</div>
  </div>
  <div class="contact-item" style="top:208px">
    <span class="ico"><svg width="16" height="16" viewBox="0 0 24 24" fill="none" stroke="#ddd" stroke-width="2"><path d="M5 3h4l2 5-2.5 1.5a11 11 0 0 0 6 6L16 13l5 2v4a2 2 0 0 1-2 2A17 17 0 0 1 3 5a2 2 0 0 1 2-2z"/></svg></span>
    <div>Phone:<br>(07) 5550 1284</div>
  </div>
  <div class="contact-item" style="top:266px">
    <span class="ico"><svg width="16" height="16" viewBox="0 0 24 24" fill="none" stroke="#ddd" stroke-width="2"><rect x="3" y="5" width="18" height="14" rx="1"/><path d="M3 6l9 7 9-7"/></svg></span>
    <div>Email:<br>info@brightvale.com.au</div>
  </div>

  <h5 style="left:924px">Quick Links</h5><div class="uline" style="left:924px"></div>
  <ul class="quick">
    <li>Home</li><li>Services</li><li>About Us</li><li>Our People</li><li>Safety &amp; Compliance</li><li>Contact</li>
  </ul>

  <div class="copyline"></div>
  <div class="copy">© Copyright 2020 Brightvale. All Rights Reserved.</div>
</footer>

</body>
</html>
```